Looking for a modern, Professional business card design

We have a simple business card, but are looking for a more modern, professional look. A sample of the basic card is attached as well as the logo. We would also like to add that we offer:
Struggling with your finances?
- Learn to become debt free
- Discover the power of cash
- Control your money instead of it controlling you
Let us help you achieve a new level of financial freedom!
Also, we would like to have a "SPECIAL OFFER!: FREE 30 minute consultation"
Financial Planning

```html
<!DOCTYPE html>
<html lang="en">
<head>
<meta charset="utf-8">
<title>Steady Ledger Coaching – Business Cards</title>
<link rel="stylesheet" href="https://fonts.googleapis.com/css2?family=Open+Sans:wght@400;600;700&display=swap">
<style>
  :root {
    --page-bg: #ecebe6;
    --green-light: #a8d44a;
    --green-mid: #8cc63f;
    --green-deep: #6aaa2a;
    --white: #ffffff;
    --ink: #1f1f1f;
    --brand-green: #5a9e1f;
  }
  * { box-sizing: border-box; margin: 0; padding: 0; }
  html, body {
    width: 1200px; height: 843px; overflow: hidden;
    background: var(--page-bg);
    font-family: "Open Sans", Arial, sans-serif;
  }
  .stage { position: relative; width: 1200px; height: 843px; }
  .card {
    position: absolute; left: 290px; width: 620px; height: 354px;
    border-radius: 4px; overflow: hidden;
    box-shadow: 0 6px 18px rgba(0,0,0,.18);
  }
  .card--back {
    top: 36px;
    background: radial-gradient(ellipse at 70% 45%, var(--green-light) 0%, var(--green-mid) 55%, var(--green-deep) 100%);
    color: var(--white);
    padding: 34px 48px;
  }
  .card--front { top: 452px; background: var(--white); }

  .brand {
    display: flex; align-items: center; gap: 12px;
    font-weight: 700; letter-spacing: .5px;
  }
  .brand__dot { border-radius: 50%; flex: none; }
  .card--back .brand { font-size: 30px; color: var(--white); margin-left: 20px; }
  .card--back .brand__dot { width: 30px; height: 30px; background: var(--white); }

  .pitch { margin-top: 28px; font-size: 15px; line-height: 1.45; }
  .pitch__title { font-weight: 700; font-size: 17px; text-transform: uppercase; }
  .pitch__list { list-style: none; margin: 4px 0 2px; }
  .pitch__list li::before { content: "• "; }
  .offer { margin-top: 10px; }
  .offer__title { font-weight: 700; font-size: 20px; text-transform: uppercase; }
  .offer__detail { font-size: 14px; font-weight: 600; text-transform: uppercase; }

  .front-art { position: absolute; inset: 0; }
  .card--front .brand {
    position: absolute; left: 34px; top: 140px; width: 220px;
    font-size: 24px; line-height: 1.15; color: var(--brand-green);
  }
  .card--front .brand__dot { width: 26px; height: 26px; background: var(--brand-green); }
  .contact {
    position: absolute; right: 44px; top: 108px;
    text-align: right; color: var(--white); font-size: 15px; line-height: 1.55;
  }
  .contact__name { font-weight: 700; font-size: 20px; text-transform: uppercase; letter-spacing: .5px; }
  .contact__role { font-size: 15px; margin-bottom: 12px; }
</style>
</head>
<body>
<main class="stage">
  <section class="card card--back">
    <div class="brand"><span class="brand__dot"></span>Steady Ledger Coaching</div>
    <div class="pitch">
      <p class="pitch__title">Struggling with your finances?</p>
      <ul class="pitch__list">
        <li>Learn to become debt free</li>
        <li>Discover the power of cash</li>
        <li>Control your money instead of it controlling you</li>
      </ul>
      <p>Let us help you achieve a new level of financial freedom!</p>
    </div>
    <div class="offer">
      <p class="offer__title">Special Offer!</p>
      <p class="offer__detail">Free 30 minute consultation</p>
    </div>
  </section>

  <section class="card card--front">
    <svg class="front-art" viewBox="0 0 620 354" width="620" height="354" aria-hidden="true">
      <defs>
        <radialGradient id="circleFill" cx="45%" cy="45%" r="60%">
          <stop offset="0" stop-color="#b5dc55"/>
          <stop offset=".6" stop-color="#8cc63f"/>
          <stop offset="1" stop-color="#6aaa2a"/>
        </radialGradient>
      </defs>
      <path d="M300 354 C250 250 270 80 420 20 C470 0 560 -4 620 0 L620 354 Z" fill="#1f1f1f"/>
      <path d="M318 354 C262 250 290 90 430 30 C480 10 560 6 620 8 L620 354 Z" fill="#ffffff"/>
      <ellipse cx="485" cy="185" rx="178" ry="178" fill="url(#circleFill)"/>
    </svg>
    <div class="brand"><span class="brand__dot"></span><span>Steady Ledger Coaching</span></div>
    <div class="contact">
      <p class="contact__name">Daniel R. Hayes</p>
      <p class="contact__role">Personal Financial Coach</p>
      <p>Cell : (205) 555-0182</p>
      <p>daniel@steadyledgercoaching.com</p>
      <p>www.steadyledgercoaching.com</p>
    </div>
  </section>
</main>
</body>
</html>
```